established boer goat stud and dorper sheep stud need an updated look

I need a design to promote the boer goat stud and dorper sheep stud, so its clear and simple
Updates

Details for business card design Wirrabel Boers and Dorper Sheep Stud. I would like silhouette animal head or full body of a boer goat (not a dairy breed goat) and Dorper sheep. Contact: Maree Dalton +61 412578304 Sandra Pollock +61 438615027 Mooroopna North Victoria Australia Email: wirrabel5184@mailvane.com

Industry/Entity Type

Agriculture

Contact Information for Business Card

Wirrabel Boers and Dorper Sheep Stud Maree Dalton +61 412578304 Sandra Pollock +61 438615027 wirrabel5184@mailvane.com Tarrawin Vale Victoria Australia

Colors
EE7325
F08F49
F5BC92
FAE3D3
FDF4ED

Requirements
Must have
• My Boer Goats and Dorper Sheep images see my photos

```html
<!DOCTYPE html>
<html lang="en">
<head>
<meta charset="utf-8">
<title>Wirrabel Boers and Dorper Stud – Business Cards</title>
<link href="https://fonts.googleapis.com/css2?family=Cinzel:wght@400;500&family=Lato:wght@400;700;900&display=swap" rel="stylesheet">
<style>
  :root{
    --bg:#b9b9b9;
    --card:#ffffff;
    --bronze:#9a6a2f;
    --navy:#2c3448;
    --grass:#7f9a55;
    --grass-dark:#5d7440;
    --straw:#b59a72;
  }
  *{margin:0;padding:0;box-sizing:border-box}
  html,body{width:1200px;height:900px;overflow:hidden;background:var(--bg)}
  .stage{position:relative;width:1200px;height:900px}
  .card{
    position:absolute;width:720px;height:390px;background:var(--card);
    box-shadow:0 6px 18px rgba(0,0,0,.35);overflow:hidden;
  }
  .card--sheep{left:60px;top:40px}
  .card--goats{left:420px;top:470px}
  .card__title{
    position:absolute;left:34px;top:30px;
    font-family:"Cinzel",serif;font-weight:400;font-size:30px;letter-spacing:1px;white-space:nowrap;
  }
  .card__title .brand{color:var(--bronze)}
  .card__title .rest{color:var(--navy)}
  .rule{position:absolute;height:3px}
  .rule--bronze{background:var(--bronze);left:30px;right:0;top:76px}
  .rule--navy{background:var(--navy);left:30px;right:0;top:262px}
  .gallery{position:absolute;left:30px;right:20px;top:88px;height:162px;display:flex;gap:6px}
  .photo{flex:1}
  .photo--sheep{background:linear-gradient(170deg,#e9e3d6 0%,#cfc6b4 35%,var(--grass) 75%,var(--grass-dark) 100%)}
  .photo--goats{background:linear-gradient(170deg,#8fae6a 0%,#e6e0d4 35%,#8a4a2c 60%,var(--straw) 100%)}
  .contact{position:absolute;font-family:"Lato",sans-serif;white-space:nowrap}
  .contact__name{left:270px;top:274px;font-size:28px;font-weight:900;color:var(--navy)}
  .contact__line{left:296px;top:314px;display:flex;align-items:baseline;gap:18px;color:var(--bronze)}
  .contact__phone{font-size:20px;letter-spacing:.5px}
  .contact__place{font-size:17px;display:inline-flex;align-items:center;gap:5px}
  .contact__email{left:140px;top:350px;font-size:21px;color:var(--bronze);display:flex;align-items:center;gap:10px}
  .icon{fill:var(--bronze)}
</style>
</head>
<body>
<div class="stage">

  <section class="card card--sheep">
    <h1 class="card__title"><span class="brand">WIRRABEL BOERS</span> <span class="rest">AND DORPER STUD</span></h1>
    <div class="rule rule--bronze"></div>
    <div class="gallery">
      <div class="photo photo--sheep" role="img" aria-label="Dorper sheep grazing in a paddock"></div>
      <div class="photo photo--sheep" role="img" aria-label="Group of Dorper sheep close up"></div>
      <div class="photo photo--sheep" role="img" aria-label="Dorper sheep feeding on grass"></div>
    </div>
    <div class="rule rule--navy"></div>
    <p class="contact contact__name">Sandra Pollock</p>
    <div class="contact contact__line">
      <span class="contact__phone">+61 438615027</span>
      <span class="contact__place">
        <svg class="icon" width="12" height="16" viewBox="0 0 12 16"><path d="M6 0C2.7 0 0 2.6 0 5.9 0 10 6 16 6 16s6-6 6-10.1C12 2.6 9.3 0 6 0zm0 8.2A2.3 2.3 0 1 1 6 3.6a2.3 2.3 0 0 1 0 4.6z"/></svg>
        Tarrawin Vale Victoria Australia
      </span>
    </div>
    <p class="contact contact__email">
      <svg class="icon" width="22" height="15" viewBox="0 0 22 15"><path d="M0 0h22v2L11 8.5 0 2z"/><path d="M0 4l11 6.5L22 4v11H0z"/></svg>
      wirrabel5184@mailvane.com
    </p>
  </section>

  <section class="card card--goats">
    <h1 class="card__title"><span class="brand">WIRRABEL BOERS</span> <span class="rest">AND DORPER STUD</span></h1>
    <div class="rule rule--bronze"></div>
    <div class="gallery">
      <div class="photo photo--goats" role="img" aria-label="Boer goats in a straw-covered yard"></div>
      <div class="photo photo--goats" role="img" aria-label="Boer goat buck standing in a yard"></div>
      <div class="photo photo--goats" role="img" aria-label="Boer goats among trees"></div>
    </div>
    <div class="rule rule--navy"></div>
    <p class="contact contact__name">Maree Dalton</p>
    <div class="contact contact__line">
      <span class="contact__phone">+61 412578304</span>
      <span class="contact__place">
        <svg class="icon" width="12" height="16" viewBox="0 0 12 16"><path d="M6 0C2.7 0 0 2.6 0 5.9 0 10 6 16 6 16s6-6 6-10.1C12 2.6 9.3 0 6 0zm0 8.2A2.3 2.3 0 1 1 6 3.6a2.3 2.3 0 0 1 0 4.6z"/></svg>
        Tarrawin Vale Victoria Australia
      </span>
    </div>
    <p class="contact contact__email">
      <svg class="icon" width="22" height="15" viewBox="0 0 22 15"><path d="M0 0h22v2L11 8.5 0 2z"/><path d="M0 4l11 6.5L22 4v11H0z"/></svg>
      wirrabel5184@mailvane.com
    </p>
  </section>

</div>
</body>
</html>
```